Beautiful design for wordpress

I need a beautiful, colourful and feminine website. My business is called 'The Velvet Lantern', and I sell crystals, books, CD's, pendulums and other metaphysical items. I also provide Reiki (energy healing).
I want this design to be eye catching and inspire happiness and joy in those who see it. And I would love to see the use of the logo and its colours :)
Please add these on the web design: Home, About, Online store, Blog

Industry/Entity Type

Business

Requirements
Must have
• Colourful and playful, must use the logo somewhere, have the words on a menu saying 'Home, Blog, Online store and about' (or similar to those)And the design must stand out!
Should not have
• grey, brown and other boring colours.

```html
<!DOCTYPE html>
<html lang="en">
<head>
<meta charset="utf-8">
<title>The Velvet Lantern – Crystals &amp; Gifts</title>
<link href="https://fonts.googleapis.com/css2?family=Mulish:wght@400;500;600;700&display=swap" rel="stylesheet">
<style>
:root{
  --sun-light:#fde894;
  --sun:#f9dc85;
  --sun-line:#f3cf72;
  --cream:#fdf1c4;
  --orange:#fba94a;
  --orange-deep:#f59b35;
  --pink:#f15fb8;
  --pink-soft:#f9b6de;
  --ink:#1f1f1f;
  --brand-ink:#5a4a3a;
  --tile-bar:#222222;
  --white:#ffffff;
  --footer:#fae08c;
  --night:#0d0d0d;
}
*{box-sizing:border-box;margin:0;padding:0}
html,body{width:1013px;height:1200px;overflow:hidden}
body{font-family:"Mulish",Arial,sans-serif;color:var(--ink);background:var(--white);position:relative}
.abs{position:absolute}

/* header */
.top-band{left:0;top:0;width:1013px;height:74px;background:var(--sun-light)}
.nav-band{left:0;top:74px;width:1013px;height:48px;background:var(--sun);border-top:1px solid var(--sun-line);border-bottom:1px solid var(--white)}
.nav-link{top:83px;height:30px;line-height:30px;font-size:13.5px;font-weight:500;color:var(--ink);text-decoration:none}
.nav-link.active{background:var(--orange);border-radius:15px;padding:0 14px;color:#3a2a10}
.search{left:771px;top:82px;width:127px;height:30px;background:var(--white);border-radius:15px;font-size:11px;color:#555;line-height:30px;padding-left:15px}
.search svg{position:absolute;right:11px;top:7px}
.brand{left:419px;top:0;width:175px;height:196px;z-index:10;background:var(--cream);border-bottom:5px solid var(--orange);display:flex;flex-direction:column;align-items:center;justify-content:center;gap:12px;padding-top:8px}
.brand-dot{width:16px;height:16px;border-radius:50%;background:var(--pink)}
.brand-name{font-size:24px;font-weight:700;color:var(--brand-ink);text-align:center;line-height:1.2}
.brand-tag{font-size:8px;font-weight:700;letter-spacing:1.6px;color:var(--brand-ink)}

/* hero */
.hero{left:0;top:122px;width:1013px;height:372px;
  background:radial-gradient(circle at 25% 35%,#d97ad0 0,transparent 18%),radial-gradient(circle at 85% 45%,#c66ac6 0,transparent 16%),radial-gradient(circle at 60% 90%,#e08ad6 0,transparent 20%),linear-gradient(135deg,#fbd3ee,#f6a9db 45%,#fcd7ef)}
.hero-caption{left:210px;top:237px;width:593px;height:161px;background:rgba(241,80,180,.62);text-align:center;color:var(--white)}
.hero-title{margin-top:26px;font-size:30px;font-weight:500;letter-spacing:.5px}
.hero-text{margin-top:6px;font-size:26px;line-height:32px;font-weight:500}
.hero-arrow{top:290px}

/* categories */
.cat-band{left:0;top:494px;width:1013px;height:182px;background:var(--orange)}
.tile{top:510px;width:190px;height:220px;box-shadow:0 1px 2px rgba(0,0,0,.25)}
.tile-img{height:166px}
.tile-label{height:54px;background:var(--tile-bar);color:var(--white);font-size:21px;line-height:54px;padding-left:11px}

/* welcome */
.welcome-title{left:99px;top:752px;font-size:26px;font-weight:500}
.welcome-copy{left:104px;top:793px;width:372px;font-size:11px;line-height:13.2px;hyphens:auto}
.welcome-copy p+p{margin-top:13px}
.reiki{left:484px;top:747px;width:431px;height:201px;background:linear-gradient(160deg,#f4f4f4,#dcdcdc 60%,#c9b6a8)}
.reiki-note{left:633px;top:760px;width:282px;height:65px;background:rgba(255,255,255,.85);text-align:right;padding:2px 14px 0 0}
.reiki-note strong{display:block;font-size:25px;font-weight:500}
.reiki-note span{font-size:16px}

/* footer */
.footer{left:0;top:958px;width:1013px;height:195px;background:var(--footer)}
.f-head{font-size:20px;font-weight:500}
.f-list{list-style:none;font-size:12px;font-weight:500;line-height:20.3px}
.thumb{width:58px;height:52px;border:1px solid var(--white)}
.contact{font-size:12px;font-weight:600;line-height:20.3px}
.social{width:33px;height:33px;border-radius:6px}
.copyright{left:0;top:1153px;width:1013px;height:47px;background:var(--night);color:var(--white);font-size:11px;text-align:center;line-height:50px}
</style>
</head>
<body>

<header>
  <div class="abs top-band"></div>
  <nav class="abs nav-band" aria-label="Main menu"></nav>
  <a class="abs nav-link active" style="left:150px" href="#">Home</a>
  <a class="abs nav-link" style="left:223px" href="#">About</a>
  <a class="abs nav-link" style="left:284px" href="#">Online store</a>
  <a class="abs nav-link" style="left:640px" href="#">Blog</a>
  <a class="abs nav-link" style="left:692px" href="#">Contact us</a>
  <div class="abs search">Search
    <svg width="16" height="16" viewBox="0 0 16 16"><circle cx="6.5" cy="6.5" r="5" fill="none" stroke="#777" stroke-width="1.6"/><line x1="10.2" y1="10.2" x2="15" y2="15" stroke="#777" stroke-width="1.8"/></svg>
  </div>
  <div class="abs brand">
    <div class="brand-dot"></div>
    <div class="brand-name">The Velvet<br>Lantern</div>
    <div class="brand-tag">CRYSTALS &amp; GIFTS</div>
  </div>
</header>

<section>
  <div class="abs hero" role="img" aria-label="Close-up of sparkling pink crystals and glitter"></div>
  <div class="abs hero-caption">
    <div class="hero-title">LORIUM IPSUM</div>
    <div class="hero-text">Neque porro quisquam est, qui dolorem<br>ipsum quia dolor sit amet, consectetur</div>
  </div>
  <svg class="abs hero-arrow" style="left:106px" width="22" height="38" viewBox="0 0 22 38"><polyline points="18,3 5,19 18,35" fill="none" stroke="#fff" stroke-width="4"/></svg>
  <svg class="abs hero-arrow" style="left:909px" width="22" height="38" viewBox="0 0 22 38"><polyline points="4,3 17,19 4,35" fill="none" stroke="#fff" stroke-width="4"/></svg>
</section>

<section>
  <div class="abs cat-band"></div>
  <a class="abs tile" style="left:97px">
    <div class="tile-img" role="img" aria-label="Cluster of blue quartz crystals" style="background:linear-gradient(180deg,#1c2540,#6d86b8 65%,#a9b7d6)"></div>
    <div class="tile-label">Crystals</div>
  </a>
  <a class="abs tile" style="left:306px">
    <div class="tile-img" role="img" aria-label="Open book in front of a bookshelf" style="background:linear-gradient(180deg,#b8a48e,#c79a6c 55%,#6f4e33)"></div>
    <div class="tile-label">Books</div>
  </a>
  <a class="abs tile" style="left:515px">
    <div class="tile-img" role="img" aria-label="Portable CD player with a disc" style="background:radial-gradient(circle at 45% 45%,#6f7a72,#c9cdca 45%,#fff 70%)"></div>
    <div class="tile-label">CD's</div>
  </a>
  <a class="abs tile" style="left:723px">
    <div class="tile-img" role="img" aria-label="Blue stone pendulum on a silver chain" style="background:radial-gradient(circle at 55% 55%,#2b47a8 0,#2a2f3a 30%,#232323 70%)"></div>
    <div class="tile-label">Pendulums</div>
  </a>
</section>

<section>
  <h1 class="abs welcome-title">Welcome</h1>
  <div class="abs welcome-copy" lang="en">
    <p>Neque porro quisquam est, qui dolorem ipsum quia dolor sit amet, consectetur, adipisci velit, sed quia non numquam eius modi tempora incidunt ut labore et dolore magnam aliquam quaerat voluptatem. Ut enim ad minima veniam, quis nostrum exercitationem ullam corporis suscipit laboriosam</p>
    <p>Neque porro quisquam est, qui dolorem ipsum quia dolor sit amet, consectetur, adipisci velit, sed quia non numquam eius modi tempora incidunt ut labore et dolore magnam aliquam quaerat voluptatem. Ut enim ad minima veniam, quis nostrum exercitationem ullam corporis suscipit laboriosam</p>
  </div>
  <div class="abs reiki" role="img" aria-label="Reiki energy healing session with a client lying down"></div>
  <div class="abs reiki-note"><strong>We also provide Reiki</strong><span>(energy healing).</span></div>
</section>

<footer>
  <div class="abs footer"></div>
  <h2 class="abs f-head" style="left:118px;top:964px">Quick Links</h2>
  <ul class="abs f-list" style="left:120px;top:996px">
    <li>Home</li><li>About</li><li>Online Store</li><li>Blog</li><li>Contact Us</li>
  </ul>

  <h2 class="abs f-head" style="left:296px;top:964px">Blog</h2>
  <div class="abs thumb" style="left:296px;top:1004px;background:linear-gradient(135deg,#e8e4e0,#b98a6a)" role="img" aria-label="Reiki session thumbnail"></div>
  <div class="abs thumb" style="left:364px;top:1004px;background:linear-gradient(135deg,#2a2a2a,#3050a8)" role="img" aria-label="Pendulum thumbnail"></div>
  <div class="abs thumb" style="left:432px;top:1004px;background:linear-gradient(135deg,#6e5a44,#d8b488)" role="img" aria-label="Open book thumbnail"></div>
  <div class="abs thumb" style="left:296px;top:1064px;background:linear-gradient(135deg,#1a1a1a,#6f6f8a)" role="img" aria-label="Hanging crystals thumbnail"></div>
  <div class="abs thumb" style="left:364px;top:1064px;background:linear-gradient(135deg,#5a0f3a,#c24a6a)" role="img" aria-label="Hands holding a lotus thumbnail"></div>
  <div class="abs thumb" style="left:432px;top:1064px;background:linear-gradient(135deg,#f4f0e4,#c9a24a)" role="img" aria-label="Brass pendulum thumbnail"></div>

  <h2 class="abs f-head" style="left:537px;top:964px">Contact</h2>
  <div class="abs contact" style="left:541px;top:998px">
    Address : xy/4 Lorium iopsum<br>sit amet, consectetur,<br>porta posuere.<br>Phone Number :&nbsp; + 60 400 1234 56
  </div>

  <h2 class="abs f-head" style="left:761px;top:962px">Follow Us</h2>
  <div class="abs social" style="left:763px;top:1005px;background:var(--orange-deep)" role="img" aria-label="Social profile one"></div>
  <div class="abs social" style="left:805px;top:1005px;background:var(--pink)" role="img" aria-label="Social profile two"></div>
  <div class="abs social" style="left:847px;top:1005px;background:#e0679f" role="img" aria-label="Social profile three"></div>

  <div class="abs copyright">© 2014.www.velvetlantern-shop.com</div>
</footer>

</body>
</html>
```